Brightwave Reach - Business Card

We need a business card for a Social Media Marketing company that specializes in online marketing for small businesses in Canada using common Social Media platforms such as Pixlora, Chatterly, Blinkpost & Quibber.

I have uploaded a copy of our logo which I would like utilized in the business card. We would like the business card to be modern yet classy design.

Our website is www.brightwavereach.ca

Industry/Entity Type

Marketing

Contact Information for Business Card

Email: info@brightwavereach.ca
Website: www.brightwavereach.ca
Telephone: 604-555-0193

Colors

Designer to choose colors to be used in the design.

Requirements
Must have
• Social Media icons on reverse
• Please add some designs with color.

```html
<!DOCTYPE html>
<html lang="en">
<head>
<meta charset="utf-8">
<title>Brightwave Reach – Business Card</title>
<link rel="stylesheet" href="https://fonts.googleapis.com/css2?family=Roboto:wght@400;500&family=Roboto+Condensed:wght@500;700&display=swap">
<style>
  :root {
    --stage: #2b2b2b;
    --card-light: #f4f4f2;
    --card-dark: #3d4043;
    --ink: #3a3c3e;
    --ink-soft: #a8a8a8;
    --paper-line: #f1f1f1;
    --rule: #9a9c9e;
  }
  * { margin: 0; padding: 0; box-sizing: border-box; }
  html, body { width: 1200px; height: 960px; overflow: hidden; }
  body { background: var(--stage); position: relative; font-family: "Roboto", Arial, sans-serif; }

  .card { position: absolute; width: 600px; height: 342px; box-shadow: 0 3px 8px rgba(0,0,0,.45); }
  .card--front { left: 314px; top: 113px; background: var(--card-light); }
  .card--back  { left: 311px; top: 472px; background: var(--card-dark); }

  .front-frame { position: absolute; left: 16px; top: 12px; right: 14px; bottom: 12px;
    border: 3px solid var(--ink); padding: 3px; }
  .front-frame::after { content: ""; position: absolute; inset: 3px; border: 1px solid var(--ink); }

  .front-mark { position: absolute; left: 0; right: 0; top: 78px; text-align: center; }
  .front-mark__dot { display: block; width: 46px; height: 46px; margin: 0 auto 8px; border-radius: 50%; background: var(--ink); }
  .front-mark__name { font-family: "Roboto Condensed", Arial, sans-serif; font-weight: 500; font-size: 13px; letter-spacing: 2px; color: var(--ink); }

  .person { position: absolute; left: 0; right: 0; top: 174px; text-align: center; }
  .person__name { font-family: "Roboto Condensed", Arial, sans-serif; font-weight: 500; font-size: 21px; line-height: 24px; color: var(--ink); letter-spacing: .3px; }
  .person__role { font-family: "Roboto Condensed", Arial, sans-serif; font-size: 15px; line-height: 18px; color: var(--ink-soft); margin-top: 2px; }
  .person__contact { font-size: 14px; color: var(--ink); line-height: 19px; margin-top: 8px; }

  .back-logo { position: absolute; left: 200px; top: 90px; width: 200px; height: 144px;
    border: 3px solid var(--paper-line); display: flex; align-items: center; justify-content: center; padding: 0 12px; }
  .back-logo__name { font-family: "Roboto Condensed", Arial, sans-serif; font-weight: 700; font-size: 28px; line-height: 32px;
    color: var(--paper-line); text-align: center; text-transform: uppercase; white-space: nowrap; }

  .social { position: absolute; left: 120px; right: 120px; top: 288px; display: flex; align-items: center; gap: 12px; }
  .social__rule { flex: 1; height: 1px; background: linear-gradient(90deg, transparent, var(--rule)); }
  .social__rule--right { background: linear-gradient(90deg, var(--rule), transparent); }
  .social__list { display: flex; gap: 10px; font-size: 12px; color: var(--paper-line); list-style: none; }
</style>
</head>
<body>
  <section class="card card--front" aria-label="Card front">
    <div class="front-frame"></div>
    <div class="front-mark">
      <span class="front-mark__dot"></span>
      <span class="front-mark__name">BRIGHTWAVE REACH</span>
    </div>
    <div class="person">
      <h1 class="person__name">ALEX MORGAN</h1>
      <p class="person__role">CEO/FOUNDER</p>
      <p class="person__contact">604-555-0193 | info@brightwavereach.ca<br>www.brightwavereach.ca</p>
    </div>
  </section>

  <section class="card card--back" aria-label="Card back">
    <div class="back-logo">
      <span class="back-logo__name">Brightwave<br>Reach</span>
    </div>
    <div class="social">
      <span class="social__rule"></span>
      <ul class="social__list">
        <li>Chatterly</li>
        <li>Pixlora</li>
        <li>Quibber</li>
      </ul>
      <span class="social__rule social__rule--right"></span>
    </div>
  </section>
</body>
</html>
```